Navoro & Omvar Automotive Repair Shop. Need a new website design.

We specialize in Navoro & Omvar auto repair, but also work on other Asian import vehicles. We have been in business for 7 years and pride ourselves on high quality auto repair that is fixed right the first time. Would like the automotive repair website to incorporate the colors black, red and white if possible and have our logo and some Navoro and Omvar vehicles included in the website.

Target Market(s)

Navoro & Omvar vehicle owners

Industry/Entity Type

Automotive Repair

Coding

Coded - Design and coding required

Number of Pages Required

5+ page

Colors
EB3D1F
EC4F4E
F09395
F8D3D4
FCEDEE

Requirements
Must have
• Home, Services, Contact Us, Schedule appointment, and a gallery tab that I can add shop pictures to when completed.
Nice to have
• Would like to see example pictures of job next to each service listed.
Should not have
• Service not related to auto repair. Ex. auto detailing, towing, car wash

```html
<!DOCTYPE html>
<html lang="en">
<head>
<meta charset="utf-8">
<title>Halvek Automotive</title>
<link href="https://fonts.googleapis.com/css2?family=Roboto+Slab:wght@300;400;500;600&display=swap" rel="stylesheet">
<style>
:root{
  --red:#dd0a0a;
  --black:#0c0c0c;
  --white:#ffffff;
  --ink:#1b1b1b;
  --muted:#555555;
  --pale:#ececec;
  --line:#d9d9d9;
}
*{box-sizing:border-box;margin:0;padding:0}
html,body{width:1200px;height:3577px;overflow:hidden}
body{position:relative;font-family:"Roboto Slab",Georgia,serif;color:var(--ink);background:var(--white)}
.abs{position:absolute}
/* top bar */
.topbar{left:0;top:0;width:1200px;height:39px;background:var(--black);color:var(--white);font-size:13px}
.topbar span{position:absolute;top:11px}
.topbar .sep{width:2px;height:22px;background:var(--red);top:8px}
/* nav */
.nav{left:0;top:39px;width:1200px;height:72px;background:var(--white)}
.nav a{position:absolute;top:26px;font-size:15px;color:var(--ink);text-decoration:none}
.btn{display:flex;align-items:center;justify-content:center;background:var(--red);color:var(--white);font-size:15px;text-decoration:none}
.nav a.btn{color:var(--white)}
.badge{left:111px;top:0;width:203px;height:205px;background:var(--white);clip-path:polygon(0 0,100% 0,100% 70%,50% 100%,0 70%);z-index:5;display:flex;flex-direction:column;align-items:center;justify-content:center;padding-bottom:40px}
.badge .dot{width:26px;height:26px;border-radius:50%;background:var(--red);margin-bottom:6px}
.badge b{font-weight:600;font-size:26px;letter-spacing:1px;color:var(--ink)}
.badge small{font-size:13px;font-weight:600;color:var(--ink);letter-spacing:2px}
/* hero */
.hero{left:0;top:111px;width:1200px;height:653px;background:linear-gradient(100deg,#3a3c3e 0%,#232426 40%,#4a4c4f 70%,#2b2c2e 100%)}
.hero-text{right:112px;top:228px;text-align:right;color:var(--white)}
.hero-text h1{font-weight:300;font-size:52px;line-height:1.1}
.hero-text h2{font-weight:600;font-size:60px;line-height:1.25}
.hero-text p{font-size:20px;line-height:28px;width:560px;margin:14px 0 0 auto;font-weight:300}
/* form */
.form{left:111px;top:694px;width:977px;height:316px;background:var(--red);color:var(--white)}
.field{position:absolute;width:217px}
.field label{display:block;font-size:17px;font-weight:500;margin-bottom:6px}
.field div{height:36px;background:var(--white);color:#666;font-size:10px;padding:12px 14px;position:relative}
.field .sel::after{content:"";position:absolute;right:12px;top:15px;border:4px solid transparent;border-top:5px solid #777}
.submit{left:384px;top:226px;width:215px;height:37px;border:2px solid var(--white);font-size:15px;display:flex;align-items:center;justify-content:center}
/* about & services */
.band{left:0;top:1010px;width:1200px;height:875px;background:linear-gradient(180deg,#e9e9e9,#f3f3f3 60%,#ebebeb)}
h3.sec{position:absolute;font-weight:500;font-size:40px;color:var(--ink)}
.about-p{left:112px;top:1160px;width:520px;font-size:15.5px;line-height:27.5px;color:#444;font-weight:300}
.cars{left:680px;top:1100px;width:495px;height:290px;border-radius:24px;background:linear-gradient(160deg,#f6f6f6 0%,#d4d6d8 45%,#8e9195 100%)}
.card{top:1565px;width:307px;height:236px;background:var(--white);border:1px solid var(--line);box-shadow:0 2px 6px rgba(0,0,0,.08);padding:30px 26px}
.card svg{display:block;margin-bottom:12px}
.card h4{font-size:18px;font-weight:500;margin-bottom:10px}
.card p{font-size:14.5px;line-height:22px;color:#555;font-weight:300}
.arrow{top:1661px;width:40px;height:40px;border-radius:50%;background:var(--black);display:flex;align-items:center;justify-content:center}
/* gallery */
.photo{width:306px;height:235px}
/* makes */
.darkband{left:0;top:3045px;width:1200px;height:532px;background:var(--black)}
.makes{left:111px;top:2694px;width:977px;height:487px;background:var(--white);box-shadow:0 2px 10px rgba(0,0,0,.12);text-align:center}
.makes h3{font-size:38px;font-weight:500;line-height:48px;margin:58px auto 0;width:900px}
.make{position:absolute;width:200px;text-align:center;font-size:22px;font-weight:600;letter-spacing:3px;color:var(--black)}
/* footer */
.foot-logo{left:108px;top:3250px;width:275px;height:236px;display:flex;flex-direction:column;align-items:center;justify-content:center;color:var(--white)}
.foot-logo .dot{width:30px;height:30px;border-radius:50%;background:var(--red);margin-bottom:10px}
.foot-logo b{font-size:40px;font-weight:600;letter-spacing:2px}
.foot-logo small{font-size:17px;letter-spacing:3px}
.fcol{color:var(--white)}
.fcol h5{font-size:20px;font-weight:500;margin-bottom:18px}
.fcol p{font-size:14px;line-height:30px}
.contact-row{position:absolute;left:0;display:flex;gap:14px;font-size:14px;line-height:20px;color:var(--white)}
.contact-row svg{flex:none;margin-top:2px}
.seal{top:3445px;width:70px;height:70px;border-radius:50%;background:var(--white)}
.rule{left:0;top:3538px;width:1200px;height:1px;background:#555}
.copy{left:0;top:3552px;width:1200px;text-align:center;color:var(--white);font-size:13px}
</style>
</head>
<body>

<header>
  <div class="abs topbar">
    <span style="left:393px">Call: 555.201.4830</span>
    <i class="sep" style="position:absolute;left:532px"></i>
    <span style="left:557px">Email: HalvekAutomotiveLLC@example.com</span>
    <i class="sep" style="position:absolute;left:843px"></i>
    <span style="left:869px">Hours of Operation: M-F 8:30-6pm</span>
  </div>
  <nav class="abs nav">
    <a href="#" style="left:347px">Home</a>
    <a href="#" style="left:432px">About Us</a>
    <a href="#" style="left:541px">Services</a>
    <a href="#" style="left:645px">Gallery</a>
    <a href="#" style="left:739px">Contact Us</a>
    <a href="#" class="btn" style="left:861px;top:15px;width:227px;height:43px">Schedule An Appointment</a>
  </nav>
  <div class="abs badge"><span class="dot"></span><b>HALVEK</b><small>AUTOMOTIVE</small></div>
</header>

<section class="abs hero" role="img" aria-label="Mechanic in a shop shirt working under a raised vehicle in the repair bay"></section>
<div class="abs hero-text">
  <h1>Welcome To</h1>
  <h2>Halvek Automotive</h2>
  <p>Halvek Automotive is a locally owned and operated auto repair shop in Cedarbrook that offers comprehensive car care and services for Navoro &amp; Omvar and all other Asian imports vehicles.</p>
  <a href="#" class="btn" style="width:187px;height:43px;margin:20px 0 0 auto">Schedule An Appointment</a>
</div>

<div class="abs band"></div>

<form class="abs form">
  <div class="field" style="left:24px;top:48px"><label>Name</label><div>Name</div></div>
  <div class="field" style="left:262px;top:48px"><label>Email Address</label><div>Email Address</div></div>
  <div class="field" style="left:500px;top:48px"><label>Year</label><div class="sel">Year</div></div>
  <div class="field" style="left:737px;top:48px"><label>Message</label><div>Message</div></div>
  <div class="field" style="left:24px;top:128px"><label>Phone</label><div>Phone</div></div>
  <div class="field" style="left:262px;top:128px"><label>Service/Repair</label><div class="sel">Choose</div></div>
  <div class="field" style="left:500px;top:128px"><label>Make</label><div class="sel">Make</div></div>
  <div class="field" style="left:737px;top:128px"><label>Model</label><div class="sel">Model</div></div>
  <div class="abs submit">Submit</div>
</form>

<h3 class="sec" style="left:113px;top:1085px">About Us</h3>
<p class="abs about-p">Led by an NMT master certified technician with 20 years experience working for Navoro &amp; Omvar dealerships, our auto shop is your go to facility for everything from factory auto maintenance, including oil changes, fluid services and tune ups, to complex engine repairs, hybrid diagnostic &amp; repair, brake jobs, etc. We have state of the art equipment and tools to ensure that we can properly diagnose and repair your vehicle to get you back on the road. Our work comes with a warranty and is fixed right the first time. We also offer discounts for RideLoop &amp; Hopcar rides.</p>
<div class="abs cars" role="img" aria-label="A white Navoro SUV and a grey Omvar sedan"></div>

<h3 class="sec" style="left:111px;top:1478px">Our Services</h3>
<div class="abs arrow" style="left:53px"><svg width="14" height="14" viewBox="0 0 14 14"><path d="M9 2L4 7l5 5" stroke="#fff" stroke-width="2.4" fill="none"/></svg></div>
<div class="abs arrow" style="left:1107px"><svg width="14" height="14" viewBox="0 0 14 14"><path d="M5 2l5 5-5 5" stroke="#fff" stroke-width="2.4" fill="none"/></svg></div>

<article class="abs card" style="left:111px">
  <svg width="40" height="40" viewBox="0 0 40 40"><rect x="4" y="18" width="32" height="14" rx="4" fill="var(--red)"/><circle cx="12" cy="33" r="4" fill="var(--red)"/><circle cx="28" cy="33" r="4" fill="var(--red)"/><path d="M27 4l5 5-3 3-5-5z" fill="var(--red)"/></svg>
  <h4>Oil Changes</h4>
  <p>Excepteur sint occaecat cupidatat non proident, sunt in culpa qui officia deserunt mollit anim id est laborum.</p>
</article>
<article class="abs card" style="left:445px">
  <svg width="40" height="40" viewBox="0 0 40 40"><rect x="2" y="6" width="36" height="24" fill="var(--red)"/><rect x="8" y="12" width="10" height="3" fill="#fff"/><rect x="8" y="19" width="14" height="3" fill="#fff"/><rect x="14" y="32" width="12" height="4" fill="var(--red)"/></svg>
  <h4>Computer Diagnostics</h4>
  <p>Excepteur sint occaecat cupidatat non proident, sunt in culpa qui officia deserunt mollit anim id est laborum.</p>
</article>
<article class="abs card" style="left:779px">
  <svg width="52" height="40" viewBox="0 0 52 40"><circle cx="14" cy="6" r="4" fill="var(--red)"/><circle cx="30" cy="6" r="4" fill="var(--red)"/><circle cx="10" cy="22" r="4" fill="var(--red)"/><circle cx="24" cy="22" r="4" fill="var(--red)"/><circle cx="38" cy="22" r="4" fill="var(--red)"/><rect x="4" y="28" width="42" height="10" rx="3" fill="var(--red)"/></svg>
  <h4>Electrical Specialists</h4>
  <p>Excepteur sint occaecat cupidatat non proident, sunt in culpa qui officia deserunt mollit anim id est laborum.</p>
</article>

<h3 class="sec" style="left:0;top:1955px;width:1200px;text-align:center">Our Gallery</h3>
<div class="abs photo" style="left:111px;top:2046px;background:linear-gradient(135deg,#8d8f92,#3d3e40)" role="img" aria-label="Technician rebuilding an engine block"></div>
<div class="abs photo" style="left:445px;top:2046px;background:linear-gradient(135deg,#4c5a66,#25292d)" role="img" aria-label="Open engine bay during repair"></div>
<div class="abs photo" style="left:780px;top:2046px;background:linear-gradient(135deg,#6c6f72,#2f3032)" role="img" aria-label="Mechanic working under a lifted vehicle"></div>
<div class="abs photo" style="left:111px;top:2310px;background:linear-gradient(135deg,#9a9ea3,#4a4d52)" role="img" aria-label="Silver truck on a lift with wheels removed"></div>
<div class="abs photo" style="left:445px;top:2310px;background:linear-gradient(135deg,#5b5c5e,#232323)" role="img" aria-label="Clutch disc and pressure plate"></div>
<div class="abs photo" style="left:780px;top:2310px;background:linear-gradient(135deg,#b83a3a,#4a2020)" role="img" aria-label="Hands installing a strut assembly on a red workbench"></div>
<a href="#" class="abs btn" style="left:529px;top:2567px;width:142px;height:41px">View All</a>

<div class="abs darkband"></div>
<section class="abs makes">
  <h3>Halvek Automotive specializes in Navoro &amp; Omvar auto repair but also service and repair the following makes:</h3>
  <span class="make" style="left:59px;top:280px">KESTRA</span>
  <span class="make" style="left:270px;top:280px">VELANTI</span>
  <span class="make" style="left:516px;top:280px">MORIKO</span>
  <span class="make" style="left:731px;top:280px">SOLVANE</span>
  <span class="make" style="left:76px;top:390px">DAEWAN</span>
  <span class="make" style="left:307px;top:390px">TARRO</span>
  <span class="make" style="left:516px;top:390px">HOSHIRA</span>
  <span class="make" style="left:731px;top:390px">RENZO</span>
</section>

<footer>
  <div class="abs foot-logo"><span class="dot"></span><b>HALVEK</b><small>AUTOMOTIVE</small></div>
  <div class="abs fcol" style="left:482px;top:3252px">
    <h5>Products</h5>
    <p>Home<br>About Us<br>Services<br>Gallery<br>Contact Us</p>
  </div>
  <div class="abs fcol" style="left:683px;top:3250px;width:260px">
    <h5>Contact Us</h5>
  </div>
  <div class="abs" style="left:652px;top:3297px;width:300px;height:120px">
    <div class="contact-row" style="top:0"><svg width="16" height="16" viewBox="0 0 16 16"><path d="M3 1l3 3-2 2c1 2 3 4 5 5l2-2 3 3-2 3C7 15 1 9 1 3z" fill="#fff"/></svg><span>555.318.2047</span></div>
    <div class="contact-row" style="top:41px"><svg width="16" height="16" viewBox="0 0 16 16"><rect x="1" y="4" width="14" height="9" fill="#fff"/><path d="M1 4l7 5 7-5" stroke="#000" fill="none"/></svg><span>HalvekAutomotiveLLC@example.com</span></div>
    <div class="contact-row" style="top:82px"><svg width="16" height="16" viewBox="0 0 16 16"><path d="M8 1a5 5 0 0 0-5 5c0 4 5 9 5 9s5-5 5-9a5 5 0 0 0-5-5z" fill="#fff"/><circle cx="8" cy="6" r="2" fill="#000"/></svg><span>418 Fairlane Court #5 Cedarbrook, TX 75000</span></div>
  </div>
  <div class="abs fcol" style="left:990px;top:3252px">
    <h5>Follow Us</h5>
    <p style="line-height:25px">Pagewall<br>Linkform<br>Snapgrid</p>
  </div>
  <div class="abs seal" style="left:731px" role="img" aria-label="Local award badge"></div>
  <div class="abs seal" style="left:826px" role="img" aria-label="Battery partner badge"></div>
  <div class="abs seal" style="left:921px" role="img" aria-label="Financing partner badge"></div>
  <div class="abs seal" style="left:1015px" role="img" aria-label="Certification badge"></div>
  <div class="abs rule"></div>
  <p class="abs copy">© 2024 Halvek Automotive LLC</p>
</footer>

</body>
</html>
```